Accounting firm needs a flyer "Brevora Group".. many job after this Stationary, business card

We need a flyer for a new company based in Melbourne Australia. We are group of young professionals who intend to provide various accounting services, taxation, finance, bookkeeping and payroll, Business service service advisory and management consulting.The main task of the firm is to provide accounting and taxation services. we then use our associates/referral partners to assist client with their legal, migration, finance needs.

We would like to see designs that match our logo, business card and letter head which I have uploaded along with this. I have also uploaded some of our website contents that might be used in flyers.
My favorite colors are: Blue (navy and royal blue), Teal (blue green), Turquoise, purple(orchid, lavender, plum).

Our brand:
Brevora Group
Where counsel runs deeper

Our mission:
To group the professionals in house, Where counsel runs deeper and turn into better business for our people, for our clients and four our communities.

We like our logo, however we are still not sure about our business card. So if we are open to work with someone who works with flyers and business card at the same time .

Target Market(s)

Individual and business client in Australia

Industry/Entity Type

Finance And Accounting

Colors
0255a3
3176b5
0493ce
33a6d7
886aae
b768aa
00a990
33b8a4

Requirements
Must have
• Brevora Group logo
• Liability limited by a scheme approved under the professional standards legislation
• Our motto: Brevora Group where counsel runs deeper
• Short description of our services:
• • Bookkeeping & Payroll
• • Finance & Capital Raising
• • Taxation, Accounting and compliances
• • Business service and advisory
• • Migration
• • Registry and Corporate Secretarial
• • Business law and legal services
• About us
• BREVORA aim to be more than just an accounting firm. We support our clients to help them achieve their personal and business goals by offering a fully integrated advisory service, helping clients to build wealth and protect their assets.We will bring together the relevant professionals across a number of specialties and locations; providing a responsive, personalised solution.
• Our mission: To group the professionals in house, Where counsel runs deeper and turn into better business for our people, for our clients and four our communities.
Nice to have
• Tax agent logo
• FLT logo

```html
<!DOCTYPE html>
<html lang="en">
<head>
<meta charset="utf-8">
<title>Brevora Group – Brochure Spreads</title>
<link href="https://fonts.googleapis.com/css2?family=Montserrat:wght@400;500;600;700;800&family=Raleway:wght@300;400&display=swap" rel="stylesheet">
<style>
:root{
  --stage:#5b5b5b;
  --navy:#14296b;
  --royal:#1f3f97;
  --blue:#0255a3;
  --sky:#0493ce;
  --teal:#00a990;
  --teal-text:#1a9a9a;
  --teal-deep:#0c4a52;
  --paper:#f4f5f7;
  --ink:#1d2440;
  --body:#4a5063;
}
*{box-sizing:border-box;margin:0;padding:0}
html,body{width:851px;height:1200px;overflow:hidden}
body{background:var(--stage);font-family:"Montserrat",sans-serif;position:relative;color:var(--ink)}
.spread{position:absolute;background:var(--paper);overflow:hidden;box-shadow:0 14px 18px rgba(0,0,0,.35)}
.spread--outside{left:72px;top:26px;width:712px;height:502px}
.spread--inside{left:71px;top:614px;width:711px;height:500px}
.abs{position:absolute}
.label{position:absolute;right:67px;color:#fff;font-family:"Raleway",sans-serif;font-weight:400;font-size:20px;letter-spacing:.5px}
.band-blue{background:linear-gradient(160deg,var(--royal),var(--navy) 70%)}
.h-sec{font-size:15px;font-weight:500;color:var(--ink)}
.h-sec b{color:var(--sky);font-weight:600}
.p-small{font-size:6px;line-height:1.45;text-align:center;color:#fff}
.p-dark{color:var(--ink)}
.brand-mark{display:flex;flex-direction:column;align-items:center;gap:4px}
.brand-dot{border-radius:50%;background:var(--blue);border:3px solid #fff;box-shadow:0 0 0 2px var(--blue)}
.brand-name{font-weight:800;color:var(--blue);letter-spacing:.5px}
.contact{font-size:6.2px;color:var(--ink);line-height:1.75}
.contact li{list-style:none;display:flex;align-items:center;gap:5px}
.contact svg{width:6px;height:6px;flex:none}
.photo{position:absolute;border-radius:8px;box-shadow:0 3px 6px rgba(0,0,0,.25)}
.svc h3{font-size:8.2px;font-weight:500;display:flex;align-items:center;gap:5px;white-space:nowrap}
.svc h3 b{font-weight:700}
.svc h3::after{content:"";flex:1;height:1px;background:currentColor;opacity:.55}
.svc p{font-size:5.2px;line-height:1.55;text-align:justify;margin-top:4px}
.svc--light h3{color:var(--ink)} .svc--light h3 b{color:var(--teal-text)} .svc--light p{color:var(--body)}
.svc--dark h3{color:#fff} .svc--dark h3 b{color:#41c6d9} .svc--dark p{color:#dbe6ee}
.web{position:absolute;font-size:8px;letter-spacing:2.4px;color:var(--ink)}
.web--light{color:#e9eef6}
</style>
</head>
<body>

<!-- OUTSIDE SPREAD -->
<section class="spread spread--outside">
  <!-- back panel -->
  <div class="abs band-blue" style="left:0;top:0;width:356px;height:236px"></div>
  <div class="abs" role="img" aria-label="Night city skyline photograph in deep blue" style="left:0;top:120px;width:356px;height:116px;background:linear-gradient(180deg,rgba(20,41,107,0),rgba(70,110,190,.45))"></div>
  <h2 class="abs h-sec" style="left:0;width:356px;top:78px;text-align:center;color:#fff"><b>About</b> Us</h2>
  <div class="abs" style="left:171px;top:98px;width:18px;height:1px;background:var(--sky)"></div>
  <p class="abs p-small" style="left:42px;top:110px;width:272px">BREVORA aim to be more than just an accounting firm. We support our clients to help them achieve their personal and business goals by offering a fully integrated advisory service, helping clients to build wealth and protect their assets. We will bring together the relevant professionals across a number of specialties and locations; providing a responsive, personalised solution.</p>

  <div class="abs brand-mark" style="left:132px;top:210px;width:100px">
    <div class="brand-dot" style="width:58px;height:58px"></div>
    <div class="brand-name" style="font-size:13px">BREVORA</div>
  </div>

  <h2 class="abs h-sec" style="left:0;width:356px;top:311px;text-align:center;font-size:13px"><b>Our</b>&nbsp; Mission</h2>
  <p class="abs p-small p-dark" style="left:28px;top:341px;width:300px">To group the professionals in house, where counsel runs deeper and turn into better business for our people, for our clients and four our communities.</p>

  <div class="abs" style="left:204px;top:409px">
    <div style="font-size:9.5px;font-weight:500"><b style="color:var(--blue);font-weight:600">Get In Touch</b> With Us</div>
    <div style="font-size:10px;font-weight:700;color:var(--blue);margin:2px 0 3px">1300 27 BREV</div>
    <ul class="contact">
      <li><svg viewBox="0 0 10 10"><path d="M5 0a3.5 3.5 0 0 0-3.5 3.5C1.5 6 5 10 5 10s3.5-4 3.5-6.5A3.5 3.5 0 0 0 5 0z" fill="var(--blue)"/></svg>Level 5, 212 Harlow Street, Melbourne</li>
      <li style="padding-left:11px;margin-top:-3px">Vic 3000</li>
      <li><svg viewBox="0 0 10 10"><circle cx="5" cy="5" r="4" fill="none" stroke="var(--blue)"/><path d="M1 5h8M5 1v8" stroke="var(--blue)" stroke-width=".8"/></svg>www.brevoragroup.com.au</li>
      <li><svg viewBox="0 0 10 10"><rect x="1" y="2" width="8" height="6" fill="none" stroke="var(--blue)"/><path d="M1 2l4 3 4-3" fill="none" stroke="var(--blue)"/></svg>info@brevoragroup.com.au</li>
      <li><svg viewBox="0 0 10 10"><path d="M2 1l2 0 1 2-1 1c.6 1.3 1.4 2.1 2.5 2.5l1-1 2 1v2c-4 0-7.5-3.5-7.5-7.5z" fill="var(--blue)"/></svg>1300 27 44 18</li>
    </ul>
  </div>

  <div class="abs" role="img" aria-label="Registered tax agent badge" style="left:18px;top:443px;width:36px;height:36px;border-radius:50%;background:#8fc641;border:3px solid #d8dbe0"></div>
  <div class="abs" style="left:72px;top:443px;display:flex;align-items:center;gap:5px">
    <div style="width:30px;height:30px;border-radius:50%;background:var(--blue)"></div>
    <div style="font-size:6px;font-weight:600;color:var(--navy);line-height:1.2">FLT<br>GUILD OF LEDGER<br>TRUSTEES</div>
  </div>

  <!-- cover panel -->
  <div class="abs band-blue" style="left:356px;top:0;width:356px;height:236px"></div>
  <h1 class="abs" style="left:356px;width:356px;top:30px;text-align:center;color:#fff;font-weight:800;font-size:21px">BREVORA GROUP</h1>
  <p class="abs" style="left:356px;width:356px;top:54px;text-align:center;color:#fff;font-family:'Raleway',sans-serif;font-weight:400;font-size:17px">WHERE COUNSEL RUNS DEEPER</p>
  <div class="abs" role="img" aria-label="Team stacking hands over a wooden desk with laptops and notebooks" style="left:396px;top:76px;width:278px;height:278px;border-radius:50%;border:8px solid #fff;background:radial-gradient(circle at 50% 45%,#c9a37a,#8a6a4c 65%,#3c3a3a);box-shadow:0 4px 10px rgba(0,0,0,.25)"></div>
  <div class="abs brand-mark" style="left:466px;top:300px;width:140px">
    <div class="brand-dot" style="width:112px;height:112px;border-width:5px"></div>
    <div class="brand-name" style="font-size:24px">BREVORA</div>
  </div>
  <div class="web" style="left:356px;width:356px;top:482px;text-align:center">www.brevoragroup.com.au</div>
</section>
<div class="label" style="top:557px">BROCHURE_OUTSIDE</div>

<!-- INSIDE SPREAD -->
<section class="spread spread--inside">
  <div class="abs" style="left:0;top:290px;width:355px;height:210px;background:linear-gradient(160deg,#0e3b45,var(--teal-deep) 60%,#0a2f3b)"></div>
  <div class="abs band-blue" style="left:355px;top:290px;width:356px;height:210px"></div>

  <h2 class="abs" style="left:0;width:330px;top:14px;text-align:center;font-size:13px;font-weight:500"><b style="color:var(--teal-text);font-weight:600">How We Can</b> Help You</h2>

  <div class="abs svc svc--light" style="left:18px;top:50px;width:198px"><h3><span><b>Bookkeeping</b> &amp; Payroll</span></h3>
    <p>Do you really want to waste time crunching the numbers and completing your bookwork when you could be spending that time on your business? Our bookkeeping team keeps accurate and updated records of all your business and personal financial activities. We manage your payroll on an ongoing basis, ensuring all employees are paid according to their employment agreements.</p></div>
  <div class="photo" role="img" aria-label="Desk with calculator, laptop and phone" style="left:225px;top:42px;width:110px;height:75px;background:linear-gradient(135deg,#e8e6e1,#9aa3ab)"></div>

  <div class="photo" role="img" aria-label="Businessman in suit reading a newspaper" style="left:18px;top:125px;width:106px;height:70px;background:linear-gradient(135deg,#c9c4bb,#3c3d44)"></div>
  <div class="abs svc svc--light" style="left:143px;top:131px;width:197px"><h3><span><b>Business Service</b> &amp; Advisory</span></h3>
    <p>While we provide peace of mind through taking care of the usual accounting and tax compliance matters, our real value lies in helping you address business challenges and uncover opportunities. We develop a deep understanding of your needs, challenges and ambitions, then tailor our advisory offering to ensure you get the attention you need, when you need it.</p></div>

  <div class="abs svc svc--light" style="left:18px;top:221px;width:190px"><h3><span><b>Taxation, Accounting</b> &amp; Compliances</span></h3>
    <p>Our experienced tax agents build close working relationships with you to understand your circumstances and develop customised solutions for your personal income tax and corporate tax exposure. Our combined approach and extensive industry experience allows us to deliver practical and relevant tax minimisation services and advice.</p></div>
  <div class="photo" role="img" aria-label="Hand holding a smartphone showing a finance app" style="left:225px;top:208px;width:110px;height:74px;background:linear-gradient(135deg,#ece6dc,#a89a88)"></div>

  <div class="photo" role="img" aria-label="Businessman buttoning a dark suit jacket" style="left:18px;top:302px;width:106px;height:57px;background:linear-gradient(135deg,#7d8790,#1b2330)"></div>
  <div class="abs svc svc--dark" style="left:143px;top:319px;width:197px"><h3><span><b>Registry</b> &amp; Corporate Secretarial</span></h3>
    <p>We understand that your corporate register, minutes and officeholder information and other secretarial registers must be kept for the life of the entity. We maintain these documents and update all registers whenever there is any change of details.</p></div>

  <div class="abs svc svc--dark" style="left:18px;top:386px;width:196px"><h3><span><b>Finance</b> &amp; Capital Raising</span></h3>
    <p>Need a second opinion? Want a better loan? Talk with us today. We regularly review client portfolios to identify opportunities and refer them to experienced finance brokers to save and assist them with a better deal or a different lender. Our brokers have all financial information at hand and make it clearly understood, giving you a far greater opportunity for approval and the most suitable finance structure, low rates, fees and product for your situation.</p></div>
  <div class="photo" role="img" aria-label="Hand writing figures in a notebook" style="left:231px;top:393px;width:104px;height:70px;background:linear-gradient(135deg,#e9e7e2,#7b7f86)"></div>
  <div class="web web--light" style="left:0;width:355px;top:486px;text-align:center">www.brevoragroup.com.au</div>

  <div class="abs svc svc--light" style="left:373px;top:20px;width:190px"><h3><span><b style="color:var(--blue)">Migration</b></span></h3>
    <p>Business innovation and employer sponsored visa applications can be complex, with the need to submit various business, financial and asset documents. We assist businesses of all sizes to make the case clear to the assessment officer. We work with highly professional migration agents and lawyers to secure your visa in the quickest time and with minimum fuss.</p></div>
  <div class="photo" role="img" aria-label="Open desert road under a pale sky" style="left:582px;top:14px;width:110px;height:74px;background:linear-gradient(180deg,#bcd3dc,#b59f8a 60%,#6b625b)"></div>

  <div class="photo" role="img" aria-label="Tablet and phone on a white desk" style="left:373px;top:94px;width:106px;height:64px;background:linear-gradient(135deg,#f2f3f5,#b9bec5)"></div>
  <div class="abs svc svc--light" style="left:498px;top:102px;width:196px"><h3><span><b style="color:var(--blue)">Management</b> Consulting Services</span></h3>
    <p>While we look after the usual accounting and tax compliance matters, our real value lies in helping you address business challenges and uncover opportunities. We develop a deep understanding of your needs and ambitions, and we work with you to tailor our consulting so you get the attention you need, when you need it.</p></div>

  <div class="abs svc svc--light" style="left:373px;top:181px;width:190px"><h3><span><b style="color:var(--blue)">Insolvency</b> &amp; Restructuring</span></h3>
    <p>Our experienced advisers build close working relationships with you to understand your circumstances and develop customised solutions for your personal and corporate exposure. This approach, combined with extensive industry experience, allows us to deliver practical and relevant restructuring advice.</p></div>
  <div class="photo" role="img" aria-label="Modern building corner against a pastel sky" style="left:582px;top:167px;width:110px;height:74px;background:linear-gradient(160deg,#c9c6e6,#e8c6cf 55%,#5a5f6e)"></div>

  <div class="abs" style="left:375px;top:246px;font-size:16px;font-weight:700;color:var(--teal-text)">BREVORA GROUP BUILD</div>
  <div class="abs" style="right:17px;top:266px;font-size:15px;font-weight:500;color:var(--ink)">YOUR BUSINESS, <b style="color:var(--teal-text);font-weight:700">GROW YOUR WEALTH</b></div>

  <div class="photo" role="img" aria-label="Fountain pen resting on a handwritten letter" style="left:373px;top:309px;width:106px;height:70px;background:linear-gradient(135deg,#e6ddd4,#a99a8c)"></div>
  <div class="abs svc svc--dark" style="left:500px;top:308px;width:194px"><h3><span><b>Business Law</b> &amp; Legal Services</span></h3>
    <p>When it comes to business law and legal services, you want a trusted, competent legal team working alongside your accountants to help you across a broad range of commercial matters. We have a strategic alliance with law firms experienced across many areas. Whether you need contracts for employees, are preparing your business for sale, or are buying one, we work with lawyers to smooth the process and deliver a favourable outcome.</p></div>

  <div class="abs" style="left:355px;width:356px;top:391px;text-align:center;color:#fff;font-family:'Raleway',sans-serif;font-weight:300;font-size:24px;line-height:1.3">YOUR <b style="font-family:'Montserrat',sans-serif;font-weight:700;color:#41c6d9">SUCCESS</b> IS<br>OUR <b style="font-family:'Montserrat',sans-serif;font-weight:700;color:#41c6d9">BUSINESS</b></div>
  <div class="web web--light" style="left:355px;width:356px;top:486px;text-align:center">www.brevoragroup.com.au</div>
</section>
<div class="label" style="top:1137px">BROCHURE_INSIDE</div>

</body>
</html>
```